Harbor Lanterns Book Cover Design

Book Cover Design Brief:
Title: Harbor Lanterns
Author: Dena Morrow
đź§­ Subtitle:
A Handbook for the Woman in the Storm or Set to Begin
🎯 Badge Text:
A Compass for Women Navigating Transformation
Trim Size: 6 x 9 inches
Total Number of Pages: Estimate 204 pages (including front/back matter and section dividers).
⸻

đź§­ Overview

Harbor Lanterns is a powerful, faith-based guide and story collection written by Dena Morrow who shares stories of 12 other women. Each chapter offers real-life insight and encouragement for women walking through the emotional wilderness of life—divorce, grief, burnout, identity shifts, loss, and uncertainty. This book isn’t about being lost in nature—it’s about navigating the unseen wilderness of the heart and soul, and finding sacred direction through faith, sisterhood, and intentional self-discovery. It’s for the woman who feels alone in what she’s going through, and is ready to rise again—with strength, clarity, and support.
đź§­ The Lantern Path
The book is grounded in Dena Morrow’s Lantern Path: Community, Openness, Mindset, Purposeful Movement, Accountability, Support, and Self-Care. This 7-part model guides readers from feeling lost to finding purpose, and the compass symbol should appear on the cover as a subtle but meaningful visual representing that inner journey.
🎨 Design Direction Must Haves
• A single woman in a wilderness-like setting (open field, mist, shoreline, etc.), visually representing emotional solitude and personal reflection • A compass or symbolic directional element integrated into the design (can be subtle—part of the background, light, path, etc.) •Mood should reflect quiet strength, inner transformation, hope and sacred guidance
Color palette: Deep greens, earthy tones, and warm golden or divine light—evoking grounding, hope, and spiritual depth
Title: Harbor Lanterns
• “Wilderness” in a natural, elegant font (same as The Harbor Lantern logo if possible) “Wisdom” in a bold serif to evoke strength and maturity
đź§­ Subtitle:
Author Name: Dena Morrow (centered or lower third, clean serif font)
Badge Text: 🎯 Badge Text:
(discreet, bottom right or near author name—no drop shadows)

Nice to Haves: Subtle visual cues of sisterhood or support in the distance (faint outlines, footsteps, horizon silhouettes) • Divine light or glow to represent God’s presence • Natural textures like breeze, water, or mist to evoke movement and transition •A sense of forward momentum—even if the woman is standing still
Should Not Have •Literal forest survival imagery •Cold or overly corporate fonts •Harsh primary colors or visual clutter
Back Cover / Spine Note The design should flow naturally into the spine and back cover. The compass and wilderness elements should feel part of the world, not placed on top of it.
Back Cover Description:
Harbor Lanterns is a healing guide and collection of real stories from women who have walked through life’s hardest seasons. Divorce, grief, abandonment, illness, burnout, addiction, estrangement, narcissistic abuse, homelessness, and the loss of loved ones are all part of the emotional wilderness this book speaks to.
If you feel lost, stuck, or unsure of who you are now, you are not alone. This book is for the woman standing in the middle of her wilderness, ready to take the next step toward healing and purpose.
Each chapter offers real truth and practical encouragement, with reflections that point you back to your strength, your True North, and the life you were made for.
Harbor Lanterns helps you reclaim faith, power, and purpose through the Lantern Path, a path shaped by values like community, mindset, and self-care.
Harbor Lanterns is a healing guide and collection of real stories from women who have walked through life’s hardest seasons. Written by life and business coach Dena Morrow, the book shares her personal journey alongside the voices of 12 courageous women. Divorce, grief, abandonment, illness, burnout, addiction, estrangement, narcissistic abuse, homelessness, and the loss of loved ones are all part of the emotional wilderness this book speaks to.

Whether you are standing in the fire or ready to rise from it, this book was written to meet you there. It is for the woman who feels stuck, shaken, or unsure of who she is now and knows something within her is ready to heal.

Each chapter offers truth and encouragement, with reflections that point you back to your strength, your True North, and the life you were made for.

With every page, you are reminded that you are not lost. You are finding your way as you engage with Dena’s story, the experiences of 12 other women, apply the tools, and move forward with clarity and courage.

Author Bio:
Dena Morrow is a life and business coach, speaker, and author who empowers women to reclaim their faith, power, and purpose after life has shaken their foundation. As the founder of The Harbor Lantern, she helps women move forward with clarity and confidence through seasons of change, loss, and transformation.

Through her coaching, workshops, and writing, Dena creates spaces where women stop feeling stuck and start rising, equipped with tools, community, and a renewed sense of direction for the life ahead.

Target Market(s)

Women ages 30-80

Industry/Entity Type

Faith Based Self Help, Spiritual Growth • Christian Living / Women’s Issues • Faith-Based Personal Development • Self-Help / Spiritual • Women’s Empowerment • Personal Transformation

Font styles to use
Serif
Sans Serif

Requirements
Must have
• A cover that visually reflects the emotional wilderness women experience during life transitions—grief, divorce, abandonment, identity loss, loss of loved one, estrangement, addiction, burnout, etc.—and the sacred path toward hope, strength, and purpose • A design that communicates both solitude and resilience, with visual cues that suggest faith, guidance, and transformation • A compass symbol or directional element subtly integrated to represent the Lantern Path (Community, Openness, Mindset, Purposeful Movement, Accountability, Support, Self-Care) • The overall tone should be inspiring, reflective, and spiritually grounded—not clinical, overly modern, or corporate • Designers are encouraged to explore concepts involving a single woman or symbolic imagery that evokes personal journey and inner navigation • Use of natural elements (landscape, light, sky, mist, etc.) is welcomed but not required—designers may propose abstract, minimalist, or layered concepts that align with the book’s message • Include the following text: • Title: Harbor Lanterns • Subtitle: đź§­ Subtitle: A Handbook for the Woman in the Storm or Set to Begin 🎯 Badge Text: A Compass for Women Navigating Transformation • Author: Dena Morrow •If you are using women they need to be real, diverse in age between 30-80 , body type and demographics
Nice to have
• A woman (or symbolic figure) in the design to reflect the personal, emotional journey of transformation • Subtle visual references to faith, sisterhood, or unseen support (e.g., faint silhouettes, glowing light, soft horizon figures, or abstract representations) • Creative use of natural elements like fog, water, paths, or sky to symbolize movement, mystery, or healing • A warm, layered color palette that transitions from darkness or shadow into light—suggesting hope and divine guidance • Textured or painterly backgrounds that feel organic and timeless • Compass elements woven into the environment (not pasted on top)—integrated as part of the visual metaphor • A sense of emotional depth or quiet strength that draws the viewer in • A design that would appeal to a wide age range of women (not too youthful or too somber)
Should not have
• Literal or clichĂ© wilderness imagery that feels like survival gear, camping, or rugged outdoor adventure • Harsh or neon colors, overly bright palettes, or anything that feels “salesy” or corporate • Clip art, cartoon-style illustrations, or flat graphics that lack emotional depth • Fonts that are overly modern, decorative, or hard to read—especially script fonts that look informal or casual • Designs that feel cold, sterile, masculine, or tech-driven • Cluttered layouts or elements that distract from the core message of faith, reflection, and transformation • Any portrayal that makes the woman look hopeless or abandoned—this is a story of resilience and rising, not despair. • A “sorority” or exclusive club feel—this book should never appear as if it’s only for a select group or the “cool girls” • Any design that suggests perfection, status, or elitism—this is about raw, real life, and inner healing • Glamour-focused imagery that disconnects from authenticity or emotional depth

```html
<!DOCTYPE html>
<html lang="en">
<head>
<meta charset="utf-8">
<title>Harbor Lanterns – Cover Spread</title>
<link href="https://fonts.googleapis.com/css2?family=Marcellus&family=Noto+Serif:ital@1&family=Roboto:wght@400&display=swap" rel="stylesheet">
<style>
  :root {
    --page: #ffffff;
    --plum: #5c0f3f;
    --cream: #ffffff;
    --ink: #1d1208;
    --back-edge: #3a1424;
    --gold-core: #fff2c4;
    --gold-mid: #e9b767;
    --violet: #5b2a6e;
  }
  html, body {
    margin: 0;
    width: 1200px;
    height: 1200px;
    overflow: hidden;
    background: var(--page);
  }
  .spread { position: relative; width: 1200px; height: 1200px; }

  /* Back cover */
  .back-cover {
    position: absolute;
    left: 47px; top: 206px;
    width: 530px; height: 794px;
    overflow: hidden;
  }
  .back-art {
    position: absolute; inset: 0;
    background:
      radial-gradient(ellipse 60% 55% at 50% 45%, rgba(70,64,52,.95) 0%, rgba(58,48,42,.9) 55%, rgba(0,0,0,0) 80%),
      linear-gradient(160deg, #6a1426 0%, var(--back-edge) 35%, #2c1a2c 70%, var(--violet) 100%);
  }
  .back-title {
    position: absolute;
    left: 0; right: 0; top: 24px;
    margin: 0;
    text-align: center;
    font-family: "Marcellus", serif;
    font-weight: 400;
    font-size: 58px;
    line-height: 56px;
    color: var(--cream);
  }
  .back-blurb {
    position: absolute;
    left: 33px; top: 152px;
    width: 464px;
    font-family: "Roboto", sans-serif;
    font-size: 12px;
    line-height: 17.2px;
    color: var(--cream);
    text-align: justify;
  }
  .back-blurb p { margin: 0 0 17px; }
  .author-photo {
    position: absolute;
    left: 0; top: 473px;
    width: 184px; height: 219px;
    background: linear-gradient(180deg, #6b5648 0%, #4a3a33 45%, #d8a13a 80%, #e0aa3c 100%);
  }
  .back-author {
    position: absolute;
    left: 199px; top: 478px;
    margin: 0;
    font-family: "Marcellus", serif;
    font-size: 32px;
    letter-spacing: 4px;
    color: var(--cream);
    font-weight: 400;
    white-space: nowrap;
  }
  .author-bio {
    position: absolute;
    left: 199px; top: 521px;
    width: 298px;
    margin: 0;
    font-family: "Roboto", sans-serif;
    font-size: 12px;
    line-height: 17.2px;
    color: var(--cream);
    text-align: justify;
  }
  .imprint {
    position: absolute;
    left: 33px; top: 738px;
    display: flex; align-items: center; gap: 8px;
    font-family: "Marcellus", serif;
    font-size: 22px;
    letter-spacing: 2px;
    color: var(--cream);
  }
  .imprint-dot { width: 10px; height: 10px; border-radius: 50%; background: var(--cream); }
  .barcode-space {
    position: absolute;
    left: 345px; top: 694px;
    width: 152px; height: 64px;
    background: #ffffff;
  }

  /* Spine */
  .spine {
    position: absolute;
    left: 577px; top: 206px;
    width: 53px; height: 794px;
    overflow: hidden;
    background: var(--page);
  }
  .spine-title, .spine-author {
    position: absolute;
    left: 50%;
    margin: 0;
    writing-mode: vertical-rl;
    transform: translateX(-50%);
    font-family: "Marcellus", serif;
    font-weight: 400;
    color: var(--plum);
    white-space: nowrap;
  }
  .spine-title { top: 26px; font-size: 42px; letter-spacing: 1px; }
  .spine-author { top: 548px; font-size: 30px; letter-spacing: 2px; }
  .spine-mark { position: absolute; left: 50%; top: 486px; transform: translateX(-50%); }

  /* Front cover */
  .front-cover {
    position: absolute;
    left: 630px; top: 206px;
    width: 530px; height: 794px;
    overflow: hidden;
    text-align: center;
  }
  .front-art {
    position: absolute; inset: 0;
    background:
      radial-gradient(ellipse 42% 40% at 50% 45%, var(--gold-core) 0%, #f7d894 35%, var(--gold-mid) 60%, rgba(180,90,60,0) 85%),
      linear-gradient(180deg, #7a1a33 0%, #b0404a 30%, #b9664a 55%, #8a2a3c 80%, var(--violet) 100%);
  }
  .tagline, .badge {
    position: absolute;
    left: 0; right: 0;
    margin: 0;
    font-family: "Noto Serif", serif;
    font-style: italic;
    letter-spacing: 1px;
  }
  .tagline { top: 48px; font-size: 22px; line-height: 28px; color: var(--ink); }
  .badge { top: 634px; font-size: 24px; line-height: 30px; color: var(--cream); }
  .front-title {
    position: absolute;
    left: 0; right: 0; top: 110px;
    margin: 0;
    font-family: "Marcellus", serif;
    font-weight: 400;
  }
  .front-title .line-one { display: block; font-size: 96px; line-height: 100px; color: var(--cream); }
  .front-title .line-two { display: block; font-size: 104px; line-height: 104px; color: var(--plum); }
  .front-author {
    position: absolute;
    left: 0; right: 0; top: 696px;
    margin: 0;
    font-family: "Marcellus", serif;
    font-weight: 400;
    font-size: 60px;
    letter-spacing: 4px;
    color: var(--cream);
    white-space: nowrap;
  }
</style>
</head>
<body>
<main class="spread">
  <section class="back-cover">
    <div class="back-art" role="img" aria-label="Painted wildflowers in deep red and violet framing a dim misty meadow"></div>
    <h2 class="back-title">Harbor<br>Lanterns</h2>
    <div class="back-blurb">
      <p>Harbor Lanterns gathers honest stories from women who have weathered the storms no one plans for. Loss, separation, sickness, exhaustion, broken trust, family distance, and sudden change all shape the dark waters this book walks through, one steady page at a time.</p>
      <p>If you feel unsteady, worn down, or unsure where you belong now, you are not the only one. This book is for the woman caught in the storm, ready to light one small lamp and take the next brave step toward home.</p>
      <p>Every chapter offers plain truth and gentle encouragement, with reflections that turn you back toward your courage, your calling, and the life still waiting for you.</p>
      <p>Harbor Lanterns helps you rebuild hope, confidence, and direction through the Lantern Path, a way of living built on friendship, rest, and faith.</p>
      <p>With every chapter, you are reminded that the shore is closer than it seems. You are finding your way as you read these stories, try the practices, and sail forward with calm and courage.</p>
    </div>
    <div class="author-photo" role="img" aria-label="Portrait photo of the author"></div>
    <h3 class="back-author">Dena Morrow</h3>
    <p class="author-bio">Lorem ipsum dolor sit amet, consectetur adipiscing elit, sed do eiusmod tempor incididunt ut labore et dolore magna aliqua. Quis ipsum suspendisse ultrices gravida. Risus commodo viverra maecenas accumsan lacus vel facilisis. Lorem ipsum dolor sit amet, consectetur adipiscing elit, sed do eiusmod tempor incididunt ut labore et dolore magna aliqua. Quis ipsum suspendisse ultrices gravida.</p>
    <div class="imprint"><span class="imprint-dot"></span>The Harbor Lantern</div>
    <div class="barcode-space"></div>
  </section>

  <section class="spine">
    <h2 class="spine-title">Harbor Lanterns</h2>
    <svg class="spine-mark" width="30" height="30" viewBox="0 0 30 30" aria-hidden="true">
      <circle cx="15" cy="15" r="11" fill="none" stroke="#5c0f3f" stroke-width="2"/>
    </svg>
    <p class="spine-author">Dena Morrow</p>
  </section>

  <section class="front-cover">
    <div class="front-art" role="img" aria-label="A woman walking away along a sunlit path through a golden misty field, framed by red and violet wildflowers"></div>
    <p class="tagline">A Handbook for the Woman in the Storm<br>or Set to Begin</p>
    <h1 class="front-title">
      <span class="line-one">Harbor</span>
      <span class="line-two">Lanterns</span>
    </h1>
    <p class="badge">A Light for Women Walking<br>Into a New Season</p>
    <p class="front-author">Dena Morrow</p>
  </section>
</main>
</body>
</html>
```